Velmora Freightway Solutions Business cards

Would like a very unique design catchy but professional for business cards. Please use log provided.Marlon WellsCeo and Founder TransCon Logistix Solutions1-888-913-3225mwells@tlsolutionsus.comwww.tlsolutionsus.com

```html
<!DOCTYPE html>
<html lang="en">
<head>
<meta charset="utf-8">
<title>Velmora Freightway Solutions – Business Cards</title>
<link rel="stylesheet" href="https://fonts.googleapis.com/css2?family=Lato:wght@400;700&display=swap">
<style>
  :root {
    --backdrop: #e6e6e6;
    --card: #ffffff;
    --brand-blue: #1471b9;
    --brand-red: #e3262d;
    --navy: #12304f;
    --ink: #2b2b2b;
    --divider: #cfcfcf;
  }
  * { box-sizing: border-box; margin: 0; padding: 0; }
  html, body {
    width: 1200px; height: 960px; overflow: hidden;
    background: var(--backdrop);
    font-family: "Lato", sans-serif;
  }
  .canvas { position: relative; width: 1200px; height: 960px; }
  .card {
    position: absolute;
    background: var(--card);
    border-radius: 28px;
    overflow: hidden;
    box-shadow: 0 4px 14px rgba(0,0,0,0.18);
  }
  .card--front { left: 237px; top: 47px; width: 720px; height: 406px; }
  .card--back  { left: 244px; top: 503px; width: 706px; height: 407px; }

  .brand-name {
    position: absolute;
    color: var(--brand-blue);
    font-weight: 700;
    text-align: center;
    letter-spacing: 0.04em;
    text-transform: uppercase;
    line-height: 1.2;
  }
  .card--front .brand-name { left: 0; right: 0; top: 196px; font-size: 38px; }
  .card--back .brand-name { left: 20px; width: 340px; top: 150px; font-size: 25px; }

  .front-web {
    position: absolute; left: 115px; right: 115px; top: 358px;
    display: flex; align-items: center; gap: 14px;
    font-size: 17px; letter-spacing: 0.14em; color: var(--navy);
  }
  .front-web .rule { flex: 1; height: 3px; background: var(--brand-blue); border-radius: 2px; }

  .divider {
    position: absolute; left: 371px; top: 66px; width: 2px; height: 246px;
    background: var(--divider);
  }
  .contact { position: absolute; left: 404px; top: 76px; color: var(--ink); }
  .contact__name { font-size: 24px; font-weight: 700; color: var(--brand-blue); line-height: 1.2; }
  .contact__title { font-size: 19px; color: var(--brand-red); text-transform: uppercase; margin-top: 4px; }
  .contact__address { font-size: 17px; line-height: 27px; margin-top: 15px; }
  .contact__list { list-style: none; margin-top: 12px; font-size: 17px; }
  .contact__list li { display: flex; align-items: center; gap: 10px; height: 30px; }
  .contact__list svg { width: 16px; height: 16px; flex: none; }

  .footer-band {
    position: absolute; left: 0; right: 0; bottom: 0; height: 78px;
    background: linear-gradient(180deg, var(--navy) 0%, var(--brand-blue) 100%);
  }
</style>
</head>
<body>
<main class="canvas">
  <section class="card card--front" aria-label="Card front">
    <h1 class="brand-name">Velmora Freightway<br>Solutions</h1>
    <div class="front-web"><span class="rule"></span><span>www.vfwayroutes.com</span><span class="rule"></span></div>
  </section>

  <section class="card card--back" aria-label="Card back">
    <h2 class="brand-name">Velmora Freightway<br>Solutions</h2>
    <div class="divider"></div>
    <div class="contact">
      <p class="contact__name">DORIAN PIKE</p>
      <p class="contact__title">CEO and Founder</p>
      <p class="contact__address">412 Harlow Creek Rd<br>Atlanta, GA 30327</p>
      <ul class="contact__list">
        <li>
          <svg viewBox="0 0 16 16"><path d="M4 1.5 6.5 4 5 6c1 2 3 4 5 5l2-1.5 2.5 2.5-2 2.5C6.5 14 2 9.5 1.5 3.5Z" fill="none" stroke="var(--brand-blue)" stroke-width="1.5" stroke-linejoin="round"/></svg>
          <span>1-888-470-6158</span>
        </li>
        <li>
          <svg viewBox="0 0 16 16"><rect x="1" y="3.5" width="14" height="9.5" rx="1.5" fill="var(--brand-blue)"/><path d="M1.5 4.5 8 9l6.5-4.5" fill="none" stroke="#fff" stroke-width="1.3"/></svg>
          <span>dpike@vfwayroutes.com</span>
        </li>
        <li>
          <svg viewBox="0 0 16 16" fill="none" stroke="var(--brand-blue)" stroke-width="1.3"><circle cx="8" cy="8" r="6.5"/><ellipse cx="8" cy="8" rx="2.8" ry="6.5"/><path d="M1.5 8h13M2.6 4.8h10.8M2.6 11.2h10.8"/></svg>
          <span>www.vfwayroutes.com</span>
        </li>
      </ul>
    </div>
    <div class="footer-band" role="img" aria-label="Decorative navy and blue wave band along the bottom edge"></div>
  </section>
</main>
</body>
</html>
```